Redesign of business card for Cedar Ridge Mechanical

We are looking for a new design for our business cards for Cedar Ridge Mechanical. We are a plumbing & HVAC construction company, operating on the West Coast of Canada and USA. Logo attached.
Industry/Entity Type
Construction - Plumbing & HVAC
Contact Information for Business Card
Name, address, phone numbers, email, website address
Look and feel
Each slider illustrates characteristics of the customer's brand and the style your logo design should communicate.

```html
<!DOCTYPE html>
<html lang="en">
<head>
<meta charset="utf-8">
<title>Cedar Ridge Mechanical – Business Card</title>
<link href="https://fonts.googleapis.com/css2?family=Poppins:wght@300;400;600&display=swap" rel="stylesheet">
<style>
  :root {
    --bg: #222325;
    --card: #232427;
    --rim: #ffffff;
    --ink: #ffffff;
    --ink-dim: #d9d9d9;
    --emboss: #141517;
    --notch: #232427;
  }
  * { margin: 0; padding: 0; box-sizing: border-box; }
  html, body { width: 1200px; height: 711px; overflow: hidden; background: var(--bg); }
  body { font-family: "Poppins", sans-serif; color: var(--ink); position: relative; }

  .card {
    position: absolute; top: 200px; width: 540px; height: 310px;
    background: var(--rim); border-radius: 24px; padding: 12px;
  }
  .card--front { left: 30px; }
  .card--back { left: 630px; }
  .card__face {
    position: relative; width: 100%; height: 100%;
    background: var(--card); border-radius: 14px;
  }
  .notch { position: absolute; background: var(--notch); }
  .notch--h { width: 6px; height: 12px; }
  .notch--top { top: -12px; }
  .notch--bottom { bottom: -12px; }
  .notch--left { left: 30px; }
  .notch--right { right: 30px; }

  .brand { display: flex; align-items: center; gap: 12px; font-weight: 600; letter-spacing: 0.5px; white-space: nowrap; }
  .brand__square { flex: none; width: 18px; height: 18px; }

  .card--front .brand {
    position: absolute; inset: 0; justify-content: center;
    color: var(--emboss); font-size: 30px;
  }
  .card--front .brand__square { background: var(--emboss); }

  .card--back .brand {
    position: absolute; left: 22px; top: 130px; width: 228px;
    color: var(--ink); font-size: 14px; gap: 9px; letter-spacing: 0.2px;
  }
  .card--back .brand__square { background: var(--ink); width: 12px; height: 12px; }

  .divider { position: absolute; left: 262px; top: 50px; width: 1px; height: 150px; background: var(--ink-dim); }

  .person { position: absolute; left: 286px; top: 46px; }
  .person__name { font-size: 22px; line-height: 1.1; }
  .person__first { font-weight: 600; }
  .person__last { font-weight: 300; }
  .person__title { font-size: 11px; font-weight: 400; margin-top: 2px; }

  .contacts { position: absolute; left: 286px; top: 118px; list-style: none; font-size: 12px; font-weight: 300; }
  .contacts li { display: flex; align-items: center; gap: 8px; line-height: 20px; }
  .contacts svg { width: 11px; height: 11px; fill: var(--ink); }

  .address {
    position: absolute; left: 0; right: 0; bottom: 24px; text-align: center;
    font-size: 12px; font-weight: 300;
  }
</style>
</head>
<body>
  <section class="card card--front" aria-label="Card front">
    <div class="card__face">
      <span class="notch notch--h notch--top notch--left"></span>
      <span class="notch notch--h notch--top notch--right"></span>
      <span class="notch notch--h notch--bottom notch--left"></span>
      <span class="notch notch--h notch--bottom notch--right"></span>
      <div class="brand"><span class="brand__square"></span>Cedar Ridge Mechanical</div>
    </div>
  </section>

  <section class="card card--back" aria-label="Card back">
    <div class="card__face">
      <span class="notch notch--h notch--top notch--left"></span>
      <span class="notch notch--h notch--top notch--right"></span>
      <span class="notch notch--h notch--bottom notch--left"></span>
      <span class="notch notch--h notch--bottom notch--right"></span>

      <div class="brand"><span class="brand__square"></span>Cedar Ridge Mechanical</div>
      <div class="divider"></div>

      <div class="person">
        <p class="person__name"><span class="person__first">Marta</span> <span class="person__last">Kovalova</span></p>
        <p class="person__title">Founder &amp; CEO</p>
      </div>

      <ul class="contacts">
        <li><svg viewBox="0 0 24 24" aria-hidden="true"><path d="M6.6 10.8a15 15 0 0 0 6.6 6.6l2.2-2.2a1 1 0 0 1 1-.25 11.4 11.4 0 0 0 3.6.57 1 1 0 0 1 1 1V20a1 1 0 0 1-1 1A17 17 0 0 1 3 4a1 1 0 0 1 1-1h3.5a1 1 0 0 1 1 1c0 1.25.2 2.45.57 3.57a1 1 0 0 1-.25 1z"/></svg>(555) 014-2290</li>
        <li><svg viewBox="0 0 24 24" aria-hidden="true"><path d="M12 2a10 10 0 1 0 0 20 10 10 0 0 0 0-20zm0 2c.9 0 2.2 2 2.8 5H9.2C9.8 6 11.1 4 12 4zM4.3 11h4.6a20 20 0 0 0 0 2H4.3a8 8 0 0 1 0-2zm.8 4h4c.3 1.6.8 3 1.5 4a8 8 0 0 1-5.5-4zm4-6h-4a8 8 0 0 1 5.5-4c-.7 1-1.2 2.4-1.5 4zm2.9 11c-.9 0-2.2-2-2.8-5h5.6c-.6 3-1.9 5-2.8 5zm3.1-9h4.6a8 8 0 0 1 0 2h-4.6a20 20 0 0 0 0-2z"/></svg>info@cedarridgemech.com</li>
        <li><svg viewBox="0 0 24 24" aria-hidden="true"><path d="M2 6l10 7 10-7v12H2zm0-2h20l-10 7z"/></svg>www.cedarridgemech.com</li>
      </ul>

      <p class="address">418 Harbor Ln. Suite 120 Bellingham, WA 98225</p>
    </div>
  </section>
</body>
</html>
```